Marwick Law Letterhead

We need a new letterhead design for a Law Firm. The address for the law firm is 1475 Calloway Street, Suite 210, Houston, Texas 77041. Phone Number: 832-361-9027; Fax Number: 832-614-7359. The logo is uploaded to the project.

```html
<!DOCTYPE html>
<html lang="en">
<head>
<meta charset="utf-8">
<title>Marwick Law Letterhead</title>
<link href="https://fonts.googleapis.com/css2?family=Montserrat:wght@400;500;600&display=swap" rel="stylesheet">
<style>
  :root {
    --backdrop: #e6e6e8;
    --paper: #ffffff;
    --brand-red: #d2161f;
    --brand-red-deep: #860a12;
    --brand-navy: #1b2f63;
    --ink: #1e1e22;
    --signature-tone: #c9c9cf;
  }
  * { box-sizing: border-box; margin: 0; padding: 0; }
  html, body {
    width: 1200px; height: 960px; overflow: hidden;
    background: var(--backdrop);
    font-family: "Montserrat", sans-serif;
    color: var(--ink);
  }
  .letterhead {
    position: absolute; left: 280px; top: 27px;
    width: 640px; height: 906px;
    background: var(--paper);
    box-shadow: 0 4px 18px rgba(0,0,0,0.12);
    overflow: hidden;
  }
  .brand {
    position: absolute; left: 56px; top: 58px;
    display: flex; align-items: center; gap: 10px;
  }
  .brand-dot {
    width: 18px; height: 18px; border-radius: 50%;
    background: var(--brand-navy);
  }
  .brand-name {
    font-family: "Montserrat", sans-serif;
    font-weight: 600; font-size: 26px; letter-spacing: 0.5px;
    color: var(--brand-navy);
  }
  .header-rule {
    position: absolute; left: 56px; right: 56px; top: 128px;
    height: 1.5px; background: var(--brand-red);
  }
  .contact-divider {
    position: absolute; left: 426px; top: 68px;
    width: 1px; height: 60px; background: var(--brand-red);
  }
  .contact {
    position: absolute; left: 438px; top: 58px;
    font-size: 9.5px; line-height: 1.4; font-weight: 500;
    font-style: normal;
  }
  .contact-line { display: flex; align-items: center; gap: 6px; }
  .contact-line svg { width: 9px; height: 9px; fill: var(--brand-red); }
  .letter {
    position: absolute; left: 96px; top: 168px; width: 440px;
    font-size: 9.2px; line-height: 1.5;
  }
  .recipient { margin-bottom: 14px; font-size: 9.8px; }
  .letter p.body-copy { margin-bottom: 16px; }
  .closing { margin-top: 20px; font-size: 10.5px; font-weight: 500; }
  .signature {
    margin-top: 6px; width: 110px; height: 26px; border-radius: 3px;
    background: var(--signature-tone);
  }
  .footer-accent {
    position: absolute; right: 0; bottom: 0;
    width: 300px; height: 180px;
    background: linear-gradient(135deg, var(--brand-red) 0%, var(--brand-red) 55%, var(--brand-red-deep) 100%);
  }
</style>
</head>
<body>
  <main class="letterhead">
    <div class="brand">
      <span class="brand-dot"></span>
      <span class="brand-name">Marwick Law</span>
    </div>

    <div class="contact-divider"></div>
    <address class="contact">
      <div>1475 Calloway Street,</div>
      <div>Suite 210, Houston,</div>
      <div>Texas 77041</div>
      <div class="contact-line">
        <svg viewBox="0 0 24 24" aria-hidden="true"><path d="M6.6 10.8a15 15 0 0 0 6.6 6.6l2.2-2.2a1 1 0 0 1 1-.25 11.4 11.4 0 0 0 3.6.57 1 1 0 0 1 1 1V20a1 1 0 0 1-1 1A17 17 0 0 1 3 4a1 1 0 0 1 1-1h3.5a1 1 0 0 1 1 1c0 1.25.2 2.45.57 3.57a1 1 0 0 1-.25 1z"/></svg>
        <span>832-361-9027</span>
      </div>
      <div class="contact-line">
        <svg viewBox="0 0 24 24" aria-hidden="true"><path d="M7 3h10v5H7zM4 9h16a2 2 0 0 1 2 2v6h-4v4H6v-4H2v-6a2 2 0 0 1 2-2zm4 7v3h8v-3z"/></svg>
        <span>832-614-7359</span>
      </div>
    </address>
    <div class="header-rule"></div>

    <article class="letter">
      <p class="recipient">Mr/s<br>First Name and Last Name<br>Company Name<br>Address</p>
      <p class="body-copy">Lorem ipsum dolor sit amet,consectetur adipiscing sed do eiusmod tempor incididunt laboreet dolore magna aliqua.Ut enim ad minim veniam, quis nostrud exercitation ullamco laboris nisi ut aliquip exea commodo consequat.Lorem ipsum dolor sit amet,consectetur adipiscing sed do eiusmod tempor incididunt labore et dolore magna aliqua. Ut enim</p>
      <p class="body-copy">Lorem ipsum dolor sit amet, consectetur adipiscing sed do eiusmod tempor incididunt labore et dolore magna aliqua. Ut enim ad minim veniam, quis nostrud exercitation ullamco laboris nisi ut aliquip exea commodo consequat.Duis aute irure dolor in reprehenderit in voluptate velit esse cillum irure dolor in reprehenderit in voluptate velit esse irure</p>
      <p class="body-copy">Lorem ipsum dolor sit amet, consectetur adipiscing sed do eiusmod tempor incididunt labore et dolore magna aliqua. consequat. Duis aute irure dolor in reprehenderit in voluptate velit esse cillum dolore eu fugiat nulla pariatur. Excepteur sint occaecat cupidatat non proident, sunt in culpa qui officia deserunt mollit,</p>
      <p class="body-copy">Lorem ipsum dolor sit amet, consectetur adipiscing sed do eiusmod tempor incididunt labore et dolore magna aliqua. Ut enim Lorem ipsum dolor sit amet, consectetur adipiscing sed do eiusmod tempor incididunt labore et dolore magna aliqua. Ut enim Lorem ipsum aliqua.ipsum</p>
      <p class="body-copy">Lorem ipsum dolor sit amet, consectetur adipiscing sed do eiusmod tempor incididunt labore et dolore magna aliqua. Ut enim ad minim veniam, quis nostrud exercitation ullamco laboris nisi ut aliquip exea commodo consequat.Duis aute irure dolor in reprehenderit in voluptate velit esse cillum irure dolor in reprehenderit in voluptate velit esse irure</p>
      <p class="body-copy">Lorem ipsum dolor sit amet, consectetur adipiscing sed do eiusmod tempor incididunt labore et dolore magna aliqua. Ut enim ad minim veniam, quis nostrud exercitation ullamco laboris nisi ut aliquip exea commodo consequat.Duis aute irure dolor in reprehenderit in voluptate velit esse cillum irure dolor in reprehenderit in voluptate velit esse irure</p>
      <p class="closing">Regards</p>
      <div class="signature" role="img" aria-label="Handwritten signature of the sender"></div>
    </article>

    <div class="footer-accent" role="img" aria-label="Decorative red and navy corner accent"></div>
  </main>
</body>
</html>
```